Harborline Renewal Business Card Design

Professional and clean design. The design colors should flow with the logo. Two-sided card with the website on the back which is:

www.HarborlineRenewal.example.

"Specializing in Water Damage Restoration"

On the front I need the name, email, phone, and logo.

Name: Darnell Quisby
Email: Darnell@HarborlineRenewal.example
Phone: 555-318-2046 for now

I only have the Preview and Thumbnail right now but should have the source files uploaded within a day or two.

Target Market(s)

Flood victims, home owners with water damage from busted pipes etc...

Industry/Entity Type

Business

Contact Information for Business Card

Name: Darnell Quisby

Font styles to use
Serif
Sans Serif

Requirements
Must have
• Business Card Details Info

```html
<!DOCTYPE html>
<html lang="en">
<head>
<meta charset="utf-8">
<title>Harborline Renewal Business Card</title>
<link rel="stylesheet" href="https://fonts.googleapis.com/css2?family=EB+Garamond:wght@400;500;700&display=swap">
<style>
  :root {
    --stage: #2b2b2d;
    --brand-blue: #2b9bd8;
    --brand-blue-deep: #1f86c4;
    --brand-blue-light: #3fb0e6;
    --card-white: #f7f7f7;
    --ink: #1e1e1e;
    --paper-white: #ffffff;
  }
  * { box-sizing: border-box; margin: 0; padding: 0; }
  html, body {
    width: 1200px; height: 900px; overflow: hidden;
    background: var(--stage);
    font-family: "EB Garamond", Georgia, serif;
  }
  .canvas {
    width: 1200px; height: 900px;
    display: flex; flex-direction: column; align-items: center; justify-content: center;
    gap: 34px;
  }
  .card {
    position: relative;
    width: 700px; height: 400px;
    overflow: hidden;
    box-shadow: 0 12px 30px rgba(0,0,0,0.45);
  }

  /* Back side */
  .card-back {
    background: linear-gradient(160deg, var(--brand-blue-light) 0%, var(--brand-blue) 55%, var(--brand-blue-deep) 100%);
    color: var(--paper-white);
  }
  .card-back .faint-mark {
    position: absolute; left: -90px; top: 110px;
    width: 330px; height: 330px; border-radius: 50%;
    background: rgba(255,255,255,0.22);
  }
  .card-back .back-content {
    position: absolute; right: 48px; top: 108px;
    text-align: right;
  }
  .card-back .wordmark {
    font-weight: 500; font-size: 34px; letter-spacing: 0.12em;
    text-transform: uppercase; color: var(--paper-white);
    margin-bottom: 26px;
  }
  .card-back .tagline {
    font-size: 21px; letter-spacing: 0.01em; margin-bottom: 6px;
  }
  .card-back .website {
    font-size: 19px; letter-spacing: 0.12em;
  }

  /* Front side */
  .card-front {
    background: var(--card-white);
    color: var(--ink);
  }
  .card-front .brand {
    position: absolute; left: 48px; top: 48px;
    display: flex; align-items: center; gap: 14px;
  }
  .card-front .brand-dot {
    width: 46px; height: 46px; border-radius: 50%;
    background: var(--brand-blue);
  }
  .card-front .wordmark {
    font-weight: 500; font-size: 25px; letter-spacing: 0.12em;
    text-transform: uppercase; color: var(--brand-blue);
  }
  .card-front .divider {
    position: absolute; left: 48px; top: 230px;
    width: 455px; height: 3px; background: var(--brand-blue);
  }
  .card-front .person-name {
    position: absolute; left: 318px; top: 190px;
    width: 190px; text-align: right;
    font-weight: 700; font-size: 26px; color: var(--brand-blue);
    white-space: nowrap;
  }
  .card-front .person-title {
    position: absolute; left: 512px; top: 224px;
    font-size: 16px; color: var(--ink);
  }
  .card-front .contact-list {
    position: absolute; left: 48px; top: 268px;
    list-style: none;
  }
  .card-front .contact-item {
    display: flex; align-items: center; gap: 12px;
    font-size: 22px; color: var(--ink);
    margin-bottom: 12px;
  }
  .card-front .contact-icon { width: 20px; height: 20px; flex: none; }
</style>
</head>
<body>
<main class="canvas">

  <section class="card card-back" aria-label="Business card back">
    <div class="faint-mark" aria-hidden="true"></div>
    <div class="back-content">
      <p class="wordmark">Harborline Renewal</p>
      <p class="tagline">Specializing in Water Damage Restoration</p>
      <p class="website">www.HarborlineRenewal.example</p>
    </div>
  </section>

  <section class="card card-front" aria-label="Business card front">
    <div class="brand">
      <span class="brand-dot" aria-hidden="true"></span>
      <span class="wordmark">Harborline Renewal</span>
    </div>

    <p class="person-name">Darnell Quisby</p>
    <div class="divider" aria-hidden="true"></div>
    <p class="person-title">Director/Owner</p>

    <ul class="contact-list">
      <li class="contact-item">
        <svg class="contact-icon" viewBox="0 0 20 20" aria-hidden="true">
          <path d="M5 3 L8 3 L9 7 L7 8.5 C8 11 9.5 12.5 12 13.5 L13.5 11.5 L17 12.5 L17 15.5 C17 16.5 16 17 15 17 C9 16.5 3.5 11 3 5 C3 4 4 3 5 3 Z" fill="var(--brand-blue)"/>
        </svg>
        <span>555-318-2046</span>
      </li>
      <li class="contact-item">
        <svg class="contact-icon" viewBox="0 0 20 20" aria-hidden="true">
          <rect x="2" y="4.5" width="16" height="11" fill="var(--brand-blue)"/>
          <path d="M2.5 5 L10 11 L17.5 5" fill="none" stroke="var(--card-white)" stroke-width="1.4"/>
        </svg>
        <span>Darnell@HarborlineRenewal.example</span>
      </li>
    </ul>
  </section>

</main>
</body>
</html>
```